Buch-/eBook-Cover für Geschichte zum Pride auf Gran Canaria
Zielgruppe
Zielgruppe: Reisefreudige junge schwule Männer
Aufgabenstellung
Die Geschichte spielt zum Pride auf Gran Canaria. Es geht um vier Freunde die dort ihre Ferien verbingen.
Ich stelle mir vor, dass auf dem Cover die Regenbogenflagge ist, Strand, Meer, keine Menschen und ein fetter Schriftzug mit dem Titel #TorvilenaGlanz. Daneben sollte kleiner mein Name Ferdinand zu Brakwede stehen. Das Cover kann aber auch gern wie ein Partyflyer designt sein und der Titel wie ein Logo wirken.
Bin aber für alternativen offen.

```html
<!DOCTYPE html>
<html lang="de">
<head>
<meta charset="utf-8">
<title>Torvilena Glanz – Ferdinand zu Brakwede</title>
<link rel="stylesheet" href="https://fonts.googleapis.com/css2?family=Bebas+Neue&display=swap">
<style>
  :root {
    --sky-top: #1aaee6;
    --sky-mid: #70c9ec;
    --haze: #e6f2f3;
    --sand-light: #ddb06c;
    --sand-deep: #c48b48;
    --sea-light: #3aa3a0;
    --sea-deep: #0e6a6c;
    --red: #d50c14;
    --orange: #f07a1a;
    --yellow: #f2d512;
    --green: #1e9a3a;
    --blue: #1e4fd0;
    --violet: #6f2bb4;
    --title: #ffffff;
  }
  html, body {
    margin: 0;
    padding: 0;
    width: 750px;
    height: 1200px;
    overflow: hidden;
    background: #ffffff;
  }
  .cover {
    position: relative;
    width: 750px;
    height: 1200px;
    overflow: hidden;
  }
  .cover-photo {
    position: absolute;
    inset: 0;
    background: linear-gradient(180deg,
      var(--sky-top) 0%,
      var(--sky-mid) 40%,
      var(--haze) 58%,
      var(--haze) 62%,
      var(--sand-light) 65%,
      var(--sand-deep) 76%,
      var(--sea-light) 80%,
      var(--sea-deep) 100%);
  }
  .cover-art {
    position: absolute;
    left: 0;
    top: 0;
    display: block;
  }
  .title-text {
    font-family: "Bebas Neue", "Oswald", sans-serif;
    fill: var(--title);
  }
  .author-name {
    font-family: "Bebas Neue", "Oswald", sans-serif;
    fill: var(--title);
  }
</style>
</head>
<body>
<div class="cover">
  <div class="cover-photo" role="img" aria-label="Luftbild: blauer Himmel über Sanddünen, Strand und türkisem Meer"></div>

  <svg class="cover-art" width="750" height="1200" viewBox="0 0 750 1200" xmlns="http://www.w3.org/2000/svg" role="img" aria-labelledby="cover-title">
    <title id="cover-title">Torvilena Glanz – Ferdinand zu Brakwede</title>
    <g class="rainbow-flag">
      <polygon points="0,72 410,118 750,165 750,248 0,152" fill="var(--red)"/>
      <polygon points="0,152 750,248 750,330 0,233" fill="var(--orange)"/>
      <polygon points="0,233 750,330 750,412 0,314" fill="var(--yellow)"/>
      <polygon points="0,314 750,412 750,494 0,395" fill="var(--green)"/>
      <polygon points="0,395 750,494 750,576 0,476" fill="var(--blue)"/>
      <polygon points="0,476 750,576 750,655 320,605 0,558" fill="var(--violet)"/>
    </g>
    <g class="cover-type">
      <text class="title-text" x="54" y="258" font-size="163" textLength="655" lengthAdjust="spacingAndGlyphs">TORVILENA</text>
      <text class="title-text" x="55" y="536" font-size="367" textLength="650" lengthAdjust="spacingAndGlyphs">GLANZ</text>
      <text class="author-name" x="705" y="595" font-size="36" text-anchor="end">FERDINAND ZU BRAKWEDE</text>
    </g>
  </svg>
</div>
</body>
</html>
```